Cleaning service website design

We need a new nice web design(logo will be the same) for a new cleaning service Company:

Informations about Company and logo you can take from flyers in attachments.

This is a cleaning service Company which have simple rules and we would like to show that(in checklist form) on website:

- What we do and that we're Cleaning Green

- Why us?

- How much(our pricing is simple)

Also we would like to communicate with clients by some nice/big pictures on website and the most important thing is our phone number and short/fast Brimtallow.

Also there should be some space for description about our Company.

Generally all information on main page can be short: about us, about service(what we do), last reviews, tips (for example: Tip of the week) and other can be some introduction to subpage where will be more information.

There will be few subpages like: About us, About our service, Photos(Before and after), Reviews , Tips, FAQ, Contact, Looking for a Job? - most of them will be just text so you can project just one example.

```html
<!DOCTYPE html>
<html lang="en">
<head>
<meta charset="utf-8">
<title>Tidy Nest House Cleaning</title>
<link href="https://fonts.googleapis.com/css2?family=Ubuntu:wght@300;400;500&family=PT+Sans:wght@400;700&display=swap" rel="stylesheet">
<style>
:root{
  --green:#6cbf5a;
  --green-dark:#4fa83e;
  --blue:#1265b3;
  --blue-light:#2a86d6;
  --navy:#0e4f92;
  --text:#888;
  --dark:#333;
  --bg:#f4f4f4;
}
*{margin:0;padding:0;box-sizing:border-box}
html,body{width:866px;height:1200px;overflow:hidden}
body{position:relative;background:var(--bg);font-family:"PT Sans",sans-serif;color:var(--text)}
.abs{position:absolute}
.topbar{left:0;top:0;width:866px;height:28px;background:var(--green)}
.search{left:594px;top:5px;width:178px;height:18px;background:#fff;border-radius:2px;font-size:7px;color:#aaa;padding:5px 6px}
.search svg{position:absolute;right:5px;top:4px}
.logo-mark{left:94px;top:48px;width:40px;height:40px;border-radius:50%;background:var(--green);border:3px solid var(--navy)}
.logo-name{left:141px;top:56px;font-family:"Ubuntu",sans-serif;font-size:19px;font-weight:500;color:var(--green-dark);white-space:nowrap}
.logo-tag{left:115px;top:104px;font-size:10px;color:var(--dark)}
.slogan{left:246px;top:64px;font-family:"Ubuntu",sans-serif;font-size:26px;font-weight:300;color:var(--green);white-space:nowrap}
.call{right:94px;top:52px;text-align:right;font-family:"Ubuntu",sans-serif;white-space:nowrap}
.call .t{font-size:22px;font-weight:300;color:var(--green);line-height:1}
.call .p{font-size:21px;color:var(--blue);line-height:1.1}
.call .u{font-size:10px;color:var(--dark)}
.nav{left:94px;top:125px;width:678px;height:44px;background:linear-gradient(#2a86d6,#0f5eaa);display:flex;font-family:"Ubuntu",sans-serif;font-size:12px}
.nav a{flex:none;color:#fff;text-decoration:none;line-height:44px;text-align:center;white-space:nowrap;border-right:1px solid rgba(0,0,0,.15)}
.nav a.on{color:#8ed27c}
.nav a:last-child{border:0}
.hero{left:94px;top:169px;width:678px;height:288px;background:linear-gradient(90deg,#d8cfc6,#eef0f2 45%,#e6e9ec 75%,#b9c6d3)}
.promo{left:508px;top:179px;width:204px;height:211px;background:var(--green);padding:12px 11px;color:#fff}
.promo h2{font-family:"Ubuntu",sans-serif;font-weight:500;font-size:17px;line-height:1.3;color:var(--navy)}
.promo ul{list-style:none;font-size:11px;line-height:17.4px;margin-top:5px}
.promo .note{position:absolute;left:14px;bottom:7px;font-size:7px}
.badge{position:absolute;left:100px;top:99px;width:95px;height:95px;border-radius:50%;background:#fff;text-align:center;color:var(--navy);font-family:"Ubuntu",sans-serif;padding-top:17px}
.badge b{display:block;font-size:11px;font-weight:500;line-height:1.35}
.badge .pr{font-size:21px;color:var(--green-dark);line-height:1.1}
.badge .s{font-size:9px}
.quote-band{left:94px;top:396px;width:678px;height:61px;background:rgba(40,40,40,.72);color:#fff;font-size:13px;padding:24px 0 0 54px}
.quote-btn{left:594px;top:411px;width:160px;height:34px;background:#fff;color:var(--green-dark);font-family:"Ubuntu",sans-serif;font-size:13px;font-weight:500;text-align:center;line-height:34px}
h3{position:absolute;font-family:"Ubuntu",sans-serif;font-weight:400;font-size:17px;color:var(--green)}
.photo{position:absolute}
.about-text{left:382px;top:515px;width:389px;font-size:9.6px;line-height:17.3px;text-align:justify}
.dolist{left:104px;top:878px;width:210px;list-style:none;font-size:8px;line-height:11.5px}
.dolist li{position:relative;padding-left:20px;margin-bottom:7.3px}
.dolist li::before{content:"";position:absolute;left:0;top:3px;width:6px;height:6px;border-radius:50%;background:#666}
.btn{position:absolute;height:21px;width:74px;background:var(--blue);color:#fff;font-size:10px;font-weight:700;text-align:center;line-height:21px}
.review{position:absolute;left:333px;width:210px;height:100px}
.review .th{position:absolute;left:0;top:0;width:86px;height:64px}
.review .txt{position:absolute;left:107px;top:-2px;width:104px}
.review h4{font-size:9.5px;color:#555;font-weight:700;line-height:12.5px}
.review p{font-size:9px;line-height:12.8px;margin-top:4px;color:#999}
.review .lk{position:absolute;left:0;top:69px;font-size:8px;color:#666;display:flex;gap:11px;align-items:center}
.lk span{display:flex;align-items:center;gap:4px}
.stars{position:absolute;left:107px;top:67px;color:#f2a823;font-size:13px;letter-spacing:1px}
.stars i{font-style:normal;color:#ccc}
.tip-text{left:556px;top:921px;width:215px;font-size:9.6px;line-height:17.3px;text-align:justify}
.footer{left:0;top:1136px;width:866px;height:64px;background:var(--green);color:#fff}
.flinks{position:absolute;left:93px;top:15px;font-size:10px;word-spacing:1px;white-space:nowrap}
.copy{position:absolute;left:93px;top:38px;font-size:9.5px}
.social{position:absolute;top:17px;width:29px;height:29px;border-radius:50%;background:#fff}
</style>
</head>
<body>
<div class="abs topbar"></div>
<div class="abs search">Type search
  <svg width="10" height="10" viewBox="0 0 10 10"><circle cx="4" cy="4" r="3" fill="none" stroke="#999" stroke-width="1.2"/><line x1="6.2" y1="6.2" x2="9" y2="9" stroke="#999" stroke-width="1.4"/></svg>
</div>

<div class="abs logo-mark"></div>
<div class="abs logo-name">Tidy Nest</div>
<div class="abs logo-tag">House Cleaning</div>
<div class="abs slogan">Simplify Your Life</div>
<div class="abs call">
  <div class="t">CALL TODAY!</div>
  <div class="p">555-014-2290</div>
  <div class="u">www.tidynestcleaning.example</div>
</div>

<nav class="abs nav">
  <a class="on" style="width:71px">Home</a><a style="width:71px">About us</a><a style="width:80px">Our service</a><a style="width:100px">Photos Gallery</a><a style="width:65px">Reviews</a><a style="width:46px">Tips</a><a style="width:47px">FAQ</a><a style="width:64px">Contact</a><a style="width:134px">Looking for a Job?</a>
</nav>

<div class="abs hero" role="img" aria-label="Smiling cleaner in yellow gloves wiping a bright white kitchen, spray bottle at right"></div>
<div class="abs promo">
  <h2>Now Serving<br>the Larkfield Region</h2>
  <ul>
    <li>Locally Owned &amp; Operated</li>
    <li>• Reliable &amp; Affordable</li>
    <li>• All Supplies Provided</li>
    <li>• Green Cleaning</li>
    <li>• Pet Friendly</li>
    <li>• No Contracts</li>
  </ul>
  <div class="badge"><b>HOUSE<br>CLEANING</b><div class="pr">$79</div><div class="s">as low as</div></div>
  <div class="note">*rates are for regular service*</div>
</div>
<div class="abs quote-band">If your home is larger than 3,000 square feet, please</div>
<div class="abs quote-btn">CALL FOR A QUOTE</div>

<h3 style="left:94px;top:485px">ABOUT US</h3>
<div class="photo" style="left:94px;top:518px;width:274px;height:163px;background:linear-gradient(120deg,#5f8a8c,#8a9f94 50%,#b8793f)" role="img" aria-label="Living room with sofa, armchair and tall wooden windows"></div>
<p class="abs about-text">Lorem ipsum dolor sit amet, consectetur adipisicing elit, sed do eiusmod tempor incididunt ut labore et dolore magna aliqua. Ut enim ad minim veniam, quis nostrud exercitation ullamco laboris nisi ut aliquip ex ea commodo consequat. Duis aute irure dolor in reprehenderit in voluptate velit esse cillum dolore eu fugiat nulla pariatur. Excepteur sint occaecat cupidatat non proident, sunt in culpa qui officia deserunt mollit anim id est laborumLorem ipsum dolor sit amet, consectetur adipisicing elit, sed do eiusmod tempor incididunt ut labore et dolore magna aliqua. Ut enim ad minim veniam, quis nostrud exercitation ullamco laboris nisi ut aliquip ex ea commodo consequat. Duis aute irure dolor in reprehenderit in voluptate velit esse cillum dolore eu fugiat nulla pariatur. Excepteur sint occaecat cupidatat non proident, sunt in culpa qui officia deserunt mollit anim id est laborum</p>

<h3 style="left:94px;top:718px">WHAT WE DO</h3>
<div class="photo" style="left:94px;top:754px;width:213px;height:111px;background:linear-gradient(90deg,#8a8f8a,#dfe3e0 50%,#b9bcb4)" role="img" aria-label="Cleaner holding a spray bottle in a modern kitchen"></div>
<ul class="abs dolist">
  <li>Thoroughly clean your bathrooms, including toilet, sink, shower and tub</li>
  <li>Carefully clean the kitchen, including the sink, countertops and boutside of appliances</li>
  <li>Tidy up around the house</li>
  <li>Dusting of surfaces</li>
  <li>Vacuuming rugs and carpeted areas</li>
  <li>Cleaning of hardwood/tile/linoleum floors</li>
  <li>Emptying Trash</li>
  <li>Making mirrors shine</li>
  <li>Make Beds</li>
</ul>
<div class="btn" style="left:94px;top:1086px">Read More</div>

<h3 style="left:325px;top:718px">LAST REVIEWS</h3>
<div class="review" style="top:761px">
  <div class="th" style="background:linear-gradient(135deg,#c9d3dc,#8f9aa4)" role="img" aria-label="Tidy home office"></div>
  <div class="txt"><h4>Lorem Ipsum is simply dummy text</h4><p>The leap into electronic typesetting, remaining essentially unchanged.</p></div>
  <div class="lk"><span><svg width="9" height="9"><circle cx="4.5" cy="4.5" r="4" fill="#6cbf5a"/></svg>Likes</span><span><svg width="9" height="9"><circle cx="4.5" cy="4.5" r="4" fill="#777"/></svg>Dislikes</span></div>
  <div class="stars">★★★<i>★★</i></div>
</div>
<div class="review" style="top:873px">
  <div class="th" style="background:linear-gradient(135deg,#d9c6a8,#8a6a4c)" role="img" aria-label="Cozy living room"></div>
  <div class="txt"><h4>Lorem Ipsum is simply dummy text</h4><p>The leap into electronic typesetting, remaining essentially unchanged.</p></div>
  <div class="lk"><span><svg width="9" height="9"><circle cx="4.5" cy="4.5" r="4" fill="#6cbf5a"/></svg>Likes</span><span><svg width="9" height="9"><circle cx="4.5" cy="4.5" r="4" fill="#777"/></svg>Dislikes</span></div>
  <div class="stars">★★★<i>★★</i></div>
</div>
<div class="review" style="top:986px">
  <div class="th" style="background:linear-gradient(135deg,#eef0f2,#d9b79a)" role="img" aria-label="Parent and child playing on a clean floor"></div>
  <div class="txt"><h4>Lorem Ipsum is simply dummy text</h4><p>The leap into electronic typesetting, remaining essentially unchanged.</p></div>
  <div class="lk"><span><svg width="9" height="9"><circle cx="4.5" cy="4.5" r="4" fill="#6cbf5a"/></svg>Likes</span><span><svg width="9" height="9"><circle cx="4.5" cy="4.5" r="4" fill="#777"/></svg>Dislikes</span></div>
  <div class="stars">★★★<i>★★</i></div>
</div>
<div class="btn" style="left:326px;top:1086px">Read More</div>

<h3 style="left:556px;top:718px">TIP OF THE WEEK</h3>
<div class="photo" style="left:556px;top:755px;width:216px;height:157px;background:linear-gradient(160deg,#e4dccf,#c9b69b 60%,#8a6b4a)" role="img" aria-label="Bright sitting room with cream sofa and window blinds"></div>
<p class="abs tip-text">Lorem ipsum dolor sit amet, consectetur adipisicing elit, sed do eiusmod tempor incididunt ut labore et dolore magna aliqua. Ut enim ad minim veniam, quis nostrud exercitation ullamco laboris nisi ut aliquip ex ea commodo consequat. Duis aute irure dolor in reprehenderit in voluptate velit esse cillum dolore eu fugiat nulla pariatur. Excepteur sint occaecat cupidatat non proident, sunt in culpa qui officia deserunt mollit anim id est laborum.</p>
<div class="btn" style="left:556px;top:1086px">Read More</div>

<footer class="abs footer">
  <div class="flinks">Home &nbsp;|&nbsp; About us &nbsp;|&nbsp; Our service &nbsp;|&nbsp; Photos Gallery &nbsp;|&nbsp; Reviews &nbsp;|&nbsp; Tips &nbsp;|&nbsp; FAQ &nbsp;|&nbsp; Contact &nbsp;|&nbsp; Looking for a Job?</div>
  <div class="copy">© 2013 brightpane ,All rights reserved</div>
  <div class="social" style="left:655px"></div>
  <div class="social" style="left:688px"></div>
  <div class="social" style="left:721px"></div>
  <div class="social" style="left:754px"></div>
</footer>
</body>
</html>
```